ORLA - Óptica Médica - web design and concept

Website concept - Create and develop our website design and structure. ORLA is an optical store chain, and we are looking to establish our web and digital concept. In attachment there are several pictures about our stores and our logo.

The website structure should be user friendly. Colors should be light and the design as simple and minimalist as possible. There are different variations of the logothat can be used, check the file.

The website will include optical collections and sun collections as an online store. Also, a medical menu should be considered in order for clients to schedule optometry appointments. There should also be a menu for client assistance where the clients can read about glass maintenance in our workshop.
Updates

Low design quality

Number of Pages Required

5+ page

Font styles to use
Serif
Sans Serif

Requirements
Must have
• Must be user-friendly and minimalist.
• Please USE PICTURES FROM THE BRANDS we sell: MERUN, BOSKA, PNW, KOLE, BAMPE
Nice to have
• Nice to inspire: ZEK glasses (see website https://ch.shopzek.com/en/)
• Nice to inspire: https://merun-eyewear.com/
• Nice to ispire: https://www.pnwglobe.com/en/
Should not have
• Hysteric colors and shapes

```html
<!DOCTYPE html>
<html lang="en">
<head>
<meta charset="utf-8">
<title>ORLA Óptica Médica</title>
<link href="https://fonts.googleapis.com/css2?family=Lato:wght@400;700;900&display=swap" rel="stylesheet">
<style>
:root{
  --gold:#ae8a4a;
  --gold-dark:#8f6f35;
  --ink:#2b2b2b;
  --line:#dcdcdc;
  --topbar:#ececec;
  --soft:#f2f2f2;
  --white:#fff;
  --black:#111;
}
*{box-sizing:border-box;margin:0;padding:0}
html,body{width:1200px;height:3141px;overflow:hidden}
body{font-family:'Lato',Arial,sans-serif;color:var(--ink);background:var(--white);position:relative}
/* top bar */
.topbar{position:absolute;left:0;top:0;width:1200px;height:52px;background:var(--topbar)}
.social{position:absolute;left:75px;top:17px;display:flex;gap:16px}
.social span{width:18px;height:18px;border-radius:50%;background:#6b6b6b;display:block}
.contact{position:absolute;right:75px;top:15px;display:flex;align-items:center;gap:14px;font-size:14px;color:#444}
.contact .item{display:flex;align-items:center;gap:10px}
.contact .cart{color:var(--gold)}
/* header */
.header{position:absolute;left:0;top:52px;width:1200px;height:95px;background:var(--white)}
.logo{position:absolute;left:75px;top:24px;display:flex;align-items:center;gap:12px;color:var(--gold);font-size:40px;font-weight:400;letter-spacing:6px}
.logo i{display:block;width:14px;height:14px;background:var(--gold)}
.nav{position:absolute;right:75px;top:41px;display:flex;gap:38px;font-size:13px;font-weight:700;color:var(--ink)}
.nav .active{color:var(--gold)}
/* hero */
.hero{position:absolute;left:0;top:147px;width:1200px;height:500px;
  background:
    linear-gradient(90deg,rgba(20,24,30,.55) 0%,rgba(20,24,30,0) 12%,rgba(0,0,0,0) 30%,rgba(25,30,90,.75) 33%,rgba(25,30,90,.75) 38%,rgba(0,0,0,0) 41%),
    linear-gradient(180deg,#d8dbe0 0%,#b6bac2 45%,#e4e6ea 70%,#c9ccd2 100%);
}
.hero::after{content:"";position:absolute;inset:0;background:linear-gradient(90deg,rgba(40,44,52,.55),rgba(40,44,52,.15) 45%,rgba(40,44,52,.25))}
.hero-copy{position:absolute;left:0;top:147px;width:1200px;text-align:center;color:var(--white)}
.hero-copy h1{position:absolute;top:150px;width:100%;font-size:50px;font-weight:900;letter-spacing:1px}
.hero-copy h2{position:absolute;top:224px;width:100%;font-size:19px;font-weight:700}
.hero-copy p{position:absolute;top:256px;width:100%;font-size:13px;font-weight:700}
.btn-dark{position:absolute;left:497px;top:298px;width:207px;height:48px;background:var(--black);color:var(--white);font-size:13px;font-weight:700;display:flex;align-items:center;justify-content:center}
.slant{position:absolute;left:0;top:620px}
.dots{position:absolute;left:75px;top:652px;display:flex;gap:6px}
.dots span{width:10px;height:10px;border-radius:50%;background:#222}
.dots span:first-child{background:var(--white);border:1px solid #222}
/* welcome */
.bg-shape{position:absolute;left:0;top:1040px}
.welcome h3{position:absolute;left:75px;top:790px;font-size:28px;font-weight:700;letter-spacing:.5px}
.welcome p{position:absolute;left:75px;top:840px;width:515px;font-size:15.5px;line-height:29px;color:#333}
.btn-gold{position:absolute;left:75px;top:977px;width:152px;height:48px;background:var(--gold);color:var(--white);font-size:13px;font-weight:700;display:flex;align-items:center;justify-content:center;border-radius:2px}
.store-photo{position:absolute;left:614px;top:760px;width:513px;height:291px;
  background:
    linear-gradient(90deg,rgba(201,152,60,.7) 0%,rgba(0,0,0,0) 8%,rgba(0,0,0,0) 92%,rgba(201,152,60,.7) 100%),
    linear-gradient(180deg,#2a2b2e 0%,#3d3c3a 30%,#6b5a45 55%,#a06a32 68%,#8a5a2a 78%,#d9d4ca 88%,#eeebe5 100%);}
/* section titles */
.sec-title{position:absolute;left:0;width:1200px;text-align:center;font-size:28px;font-weight:700;color:#333;letter-spacing:.5px}
.sec-sub{position:absolute;left:0;width:1200px;text-align:center;font-size:16px;color:#333}
/* guarantees */
.guarantee{position:absolute;top:1252px;width:241px;height:283px;background:var(--white);border:1px solid var(--line);border-radius:8px;text-align:center;padding:32px 18px 0}
.guarantee svg{display:block;margin:0 auto 20px;height:56px}
.guarantee h4{color:var(--gold);font-size:16px;font-weight:700;line-height:24px;margin-bottom:8px}
.guarantee p{font-size:14px;line-height:23px;color:#333}
/* shop */
.product{position:absolute;top:1707px;width:241px;height:328px;border:1px solid var(--line);background:var(--white);text-align:center}
.product .pic{display:block;margin:26px auto 0;width:215px;height:118px;border-radius:4px}
.product h5{margin-top:28px;font-size:16px;font-weight:700}
.product p{margin:8px auto 0;width:200px;font-size:13px;line-height:21px;color:#333}
.product .price{margin-top:8px;font-size:19px;font-weight:700;color:var(--gold)}
.product .add{margin:10px auto 0;width:112px;height:32px;border:1px solid #333;border-radius:3px;font-size:12px;font-weight:700;display:flex;align-items:center;justify-content:center}
.arrow{position:absolute;top:1858px}
/* brands */
.brands-bg{position:absolute;left:0;top:2100px}
.brand{position:absolute;top:2211px;width:191px;height:90px;background:var(--white);border:1px solid var(--line);display:flex;align-items:center;justify-content:center;font-size:22px;font-weight:900;color:var(--black);letter-spacing:2px}
/* blog */
.blog{position:absolute;left:0;top:2374px;width:1200px;height:581px;
  background:
    linear-gradient(180deg,rgba(90,60,20,.25) 0%,rgba(0,0,0,0) 20%,rgba(0,0,0,0) 80%,rgba(90,60,20,.3) 100%),
    linear-gradient(110deg,#8f6c34 0%,#c19b5b 30%,#d2b27a 50%,#b48f52 72%,#8c6a33 100%);}
.blog .sec-title{color:var(--white);top:52px}
.feature{position:absolute;left:75px;top:2496px;width:511px;height:411px;
  background:
    linear-gradient(90deg,#5c6a76 0%,#8c8e8a 30%,#c8c9c7 55%,#e6d24a 80%,#f0e060 100%);}
.feature::after{content:"";position:absolute;left:0;right:0;bottom:0;height:230px;background:linear-gradient(200deg,rgba(0,0,0,0) 10%,rgba(120,200,60,.8) 40%,rgba(170,60,150,.9) 70%,#241a26 100%)}
.feature-shade{position:absolute;left:75px;top:2770px;width:511px;height:137px;background:linear-gradient(180deg,rgba(0,0,0,0),rgba(0,0,0,.8))}
.feature-copy{position:absolute;left:98px;top:2790px;width:470px;color:var(--white)}
.feature-copy .date{font-size:13px;font-weight:700}
.feature-copy h6{font-size:15px;font-weight:700;margin-top:8px}
.feature-copy p{font-size:14px;line-height:23px;margin-top:10px}
.thumb{position:absolute;left:614px;width:178px;height:126px}
.post{position:absolute;left:814px;width:300px;color:var(--white)}
.post .date{font-size:13px;font-weight:700}
.post h6{font-size:15px;font-weight:700;margin-top:6px}
.post p{font-size:14px;line-height:22px;margin-top:8px;color:#f6ecd9}
/* footer */
.footer-nav{position:absolute;left:75px;top:2998px;display:flex;gap:36px;font-size:12px;font-weight:700}
.copy{position:absolute;left:75px;top:3044px;font-size:12px;line-height:23px;color:#444}
.signup h6{position:absolute;left:792px;top:2997px;font-size:18px;font-weight:700}
.signup .field{position:absolute;left:792px;top:3037px;width:283px;height:40px;border:1px solid var(--line);font-size:12px;color:#333;padding:12px 14px}
.signup .go{position:absolute;left:1075px;top:3037px;width:50px;height:40px;background:var(--gold);color:var(--white);font-weight:700;font-size:14px;display:flex;align-items:center;justify-content:center}
</style>
</head>
<body>

<div class="topbar">
  <div class="social" aria-label="Social links"><span></span><span></span><span></span><span></span><span></span></div>
  <div class="contact">
    <div class="item">
      <svg width="14" height="14" viewBox="0 0 24 24"><path fill="#ae8a4a" d="M6.6 10.8a15 15 0 0 0 6.6 6.6l2.2-2.2c.3-.3.7-.4 1-.2 1.1.4 2.3.6 3.6.6.6 0 1 .4 1 1V20c0 .6-.4 1-1 1A17 17 0 0 1 3 4c0-.6.4-1 1-1h3.5c.6 0 1 .4 1 1 0 1.3.2 2.5.6 3.6.1.3 0 .7-.2 1z"/></svg>
      <strong>900 12 34 56</strong>
    </div>
    <div class="item" style="margin-left:14px">
      <svg width="16" height="12" viewBox="0 0 16 12"><rect width="16" height="12" rx="1" fill="#ae8a4a"/><path d="M1 1l7 5 7-5" stroke="#fff" fill="none" stroke-width="1.3"/></svg>
      <span>orlaoptica@mailbox.com</span>
    </div>
    <svg style="margin-left:26px" width="16" height="16" viewBox="0 0 16 16"><circle cx="6.5" cy="6.5" r="5" stroke="#555" stroke-width="2" fill="none"/><path d="M10 10l5 5" stroke="#555" stroke-width="2"/></svg>
    <svg width="14" height="15" viewBox="0 0 14 15"><circle cx="7" cy="4" r="3.5" fill="#555"/><path d="M0 15c0-4 3-6.5 7-6.5s7 2.5 7 6.5z" fill="#555"/></svg>
    <span class="cart">
      <svg width="16" height="14" viewBox="0 0 16 14"><path d="M0 1h3l2 8h8l2-6H4" stroke="#ae8a4a" stroke-width="1.6" fill="none"/><circle cx="6" cy="12.5" r="1.4" fill="#ae8a4a"/><circle cx="12" cy="12.5" r="1.4" fill="#ae8a4a"/></svg> (0)
    </span>
  </div>
</div>

<header class="header">
  <div class="logo"><i></i>ORLA</div>
  <nav class="nav"><span class="active">HOME</span><span>ABOUT US</span><span>PRODUCTS</span><span>CONTACT</span><span>BLOG</span><span>STORE</span></nav>
</header>

<div class="hero" role="img" aria-label="Photo of the optical store interior with eyewear wall displays and examination chair"></div>
<div class="hero-copy">
  <h1>ORLA OPTICA</h1>
  <h2>BOOK YOUR APPOINTMENT WITH US.</h2>
  <p>We will be happy to help you and offer you the best solution for your visual health problems.</p>
  <div class="btn-dark">BOOK AN APPOINTMENT</div>
</div>
<svg class="slant" width="1200" height="70" viewBox="0 0 1200 70"><polygon points="0,15 1200,0 1200,14 0,64" fill="#ae8a4a"/></svg>
<div class="dots"><span></span><span></span><span></span><span></span></div>

<svg class="bg-shape" width="1200" height="560" viewBox="0 0 1200 560"><polygon points="1200,0 1200,556 0,556 0,540" fill="#f2f2f2"/></svg>

<section class="welcome">
  <h3>WELCOME TO ORLA OPTICS</h3>
  <p>ORLA OPTICA opens its doors with a clear purpose: to take care of you.&nbsp; Our priority is your visual health, and for this reason we have the best&nbsp; professionals and the most competitive products to serve your needs.</p>
  <div class="btn-gold">READ MORE</div>
  <div class="store-photo" role="img" aria-label="Photo of the store showroom with wooden counter and illuminated wall displays"></div>
</section>

<section class="guarantees">
  <h3 class="sec-title" style="top:1140px">OUR GUARANTEES</h3>
  <p class="sec-sub" style="top:1194px">Aliquam molestie, mi et imperdiet euismod, dui purus auctor tellus, et interdum lacus lectus et ante.</p>

  <div class="guarantee" style="left:75px">
    <svg viewBox="0 0 40 56" width="40"><circle cx="20" cy="8" r="7" fill="#ae8a4a"/><path d="M4 16l8 6h16l8-6 3 4-9 7v12l3 15h-7l-4-13-4 13h-7l3-15V27L1 20z" fill="#ae8a4a"/></svg>
    <h4>ORLA CHILDHOOD<br>GUARANTEE</h4>
    <p>50% discount on new glasses, if your child's graduation has changed before<br>six months.</p>
  </div>
  <div class="guarantee" style="left:345px">
    <svg viewBox="0 0 40 56" width="40"><path d="M10 30l-6 22 8-4 5 7 3-20zM30 30l6 22-8-4-5 7-3-20z" fill="#333"/><circle cx="20" cy="20" r="17" fill="#333"/><circle cx="20" cy="20" r="11" fill="#fff"/><path d="M20 13l2.2 4.6 5 .7-3.6 3.5.9 5-4.5-2.4-4.5 2.4.9-5-3.6-3.5 5-.7z" fill="#333"/></svg>
    <h4>ORLA ACCIDENT<br>WARRANTY</h4>
    <p>Did you get off your glasses when you got out of the car? Did your little boy play with his sunglasses?</p>
  </div>
  <div class="guarantee" style="left:614px">
    <svg viewBox="0 0 40 56" width="36"><path d="M10 26V18a10 10 0 0 1 20 0v8" stroke="#333" stroke-width="5" fill="none"/><rect x="4" y="26" width="32" height="28" rx="3" fill="#333"/></svg>
    <h4>ORLA SECURITY</h4>
    <p>If you have suffered a robbery or robbery in your home, you will opt for the replacement of the same product at<br>half price.</p>
  </div>
  <div class="guarantee" style="left:884px">
    <svg viewBox="0 0 60 56" width="60"><path d="M2 28C10 14 20 8 30 8s20 6 28 20C50 42 40 48 30 48S10 42 2 28z" fill="#333"/><circle cx="30" cy="28" r="13" fill="#fff"/><circle cx="30" cy="28" r="8" fill="#333"/></svg>
    <h4>ORLA VISION</h4>
    <p>If you suffer from a diagnosed visual pathology and during the first two years your graduation changes, we replenish your crystals to 50%.</p>
  </div>
</section>

<section class="shop">
  <h3 class="sec-title" style="top:1648px">SHOP</h3>
  <svg class="arrow" style="left:44px" width="16" height="26" viewBox="0 0 16 26"><path d="M13 2L3 13l10 11" stroke="#777" stroke-width="3" fill="none"/></svg>
  <svg class="arrow" style="left:1138px" width="16" height="26" viewBox="0 0 16 26"><path d="M3 2l10 11L3 24" stroke="#777" stroke-width="3" fill="none"/></svg>

  <div class="product" style="left:75px">
    <div class="pic" role="img" aria-label="Product photo of red rectangular eyeglasses" style="background:linear-gradient(180deg,#f6efee 0%,#d9a9a2 45%,#b5584c 55%,#f3e8e6 100%)"></div>
    <h5>Product Name</h5><p>Aliquam molestie, mi et lobortis imperdiet euismod</p><div class="price">$2.99</div><div class="add">Add to Cart</div>
  </div>
  <div class="product" style="left:345px">
    <div class="pic" role="img" aria-label="Product photo of black frame eyeglasses" style="background:linear-gradient(180deg,#f4f4f4 0%,#b9b9b9 45%,#3a3a3a 55%,#efefef 100%)"></div>
    <h5>Product Name</h5><p>Aliquam molestie, mi et lobortis imperdiet euismod</p><div class="price">$2.99</div><div class="add">Add to Cart</div>
  </div>
  <div class="product" style="left:614px">
    <div class="pic" role="img" aria-label="Product photo of tortoiseshell eyeglasses" style="background:linear-gradient(180deg,#f6efe8 0%,#c99a70 45%,#7a3e1c 55%,#f3e9df 100%)"></div>
    <h5>Product Name</h5><p>Aliquam molestie, mi et lobortis imperdiet euismod</p><div class="price">$2.99</div><div class="add">Add to Cart</div>
  </div>
  <div class="product" style="left:884px">
    <div class="pic" role="img" aria-label="Product photo of a turquoise contact lens case" style="background:radial-gradient(ellipse 60% 60% at 45% 55%,#1fb5b0 0%,#4fcfca 35%,#b9dcdc 65%,#eef3f3 100%)"></div>
    <h5>Product Name</h5><p>Aliquam molestie, mi et lobortis imperdiet euismod</p><div class="price">$2.99</div><div class="add">Add to Cart</div>
  </div>
</section>

<svg class="brands-bg" width="1200" height="274" viewBox="0 0 1200 274"><rect width="1200" height="274" fill="#f2f2f2"/><polygon points="1200,0 1200,120 500,274 1200,274" fill="#f7f7f7"/></svg>
<section class="brands">
  <h3 class="sec-title" style="top:2150px">OUR BRANDS</h3>
  <div class="brand" style="left:75px">WARDEN</div>
  <div class="brand" style="left:289px;font-size:19px;letter-spacing:0">NINA ROCA</div>
  <div class="brand" style="left:505px;font-size:20px">VELLANO</div>
  <div class="brand" style="left:720px;font-size:14px;letter-spacing:1px">MARISA DELGADO</div>
  <div class="brand" style="left:934px;font-size:21px">STRADA</div>
</section>

<section class="blog" role="img" aria-label="Warm gold-toned photo of an optometry examination room">
  <h3 class="sec-title">BLOG POSTS</h3>
</section>
<div class="feature" role="img" aria-label="Blog cover photo about sun protection with mirrored sunglasses"></div>
<div class="feature-shade"></div>
<div class="feature-copy">
  <div class="date">MAR, 20, 2018</div>
  <h6>LOREM IPSUM DOLOR SIT AMET..</h6>
  <p>Aliquam molestie, mi et imperdiet euismod, dui purus auctor tellus, et interdum lacus lectus et ante...</p>
</div>

<div class="thumb" style="top:2496px;background:linear-gradient(90deg,#6a5a4c 0%,#a08070 35%,#f0c030 60%,#3a6fc0 100%)" role="img" aria-label="Blog thumbnail for an opinion article"></div>
<div class="post" style="top:2496px"><div class="date">JUNE, 26, 2018</div><h6>LOREM IPSUM DOLOR SIT AMET..</h6><p>Aliquam molestie, mi et imperdiet euismod, dui purus auctor tellus, et interdum lacus lectus et ante...</p></div>

<div class="thumb" style="top:2638px;background:linear-gradient(90deg,#7a7f86 0%,#c8a890 40%,#8faed6 75%,#5e86c4 100%)" role="img" aria-label="Blog thumbnail for an eyelid care article"></div>
<div class="post" style="top:2638px"><div class="date">JUNE, 26, 2018</div><h6>LOREM IPSUM DOLOR SIT AMET..</h6><p>Aliquam molestie, mi et imperdiet euismod, dui purus auctor tellus, et interdum lacus lectus et ante...</p></div>

<div class="thumb" style="top:2781px;background:linear-gradient(90deg,#6e5f6a 0%,#b88a80 30%,#d9489a 55%,#f0c23c 78%,#3f9c5e 100%)" role="img" aria-label="Blog thumbnail for an article about colour vision"></div>
<div class="post" style="top:2781px"><div class="date">JUNE, 26, 2018</div><h6>LOREM IPSUM DOLOR SIT AMET..</h6><p>Aliquam molestie, mi et imperdiet euismod, dui purus auctor tellus, et interdum lacus lectus et ante...</p></div>

<footer>
  <nav class="footer-nav"><span>HOME</span><span>ABOUT US</span><span>PRODUCTS</span><span>CONTACT</span><span>BLOG</span><span>STORE</span></nav>
  <div class="copy">Copyright © 2018. Company Name.<br>All Right Reserved</div>
  <div class="signup">
    <h6>EMAIL SIGN UP</h6>
    <div class="field">Enter Email Address</div>
    <div class="go">GO</div>
  </div>
</footer>

</body>
</html>
```